Business Card Design

Company is a Commercial Building Company specialising in New Construction and existing refurbishments

Industry/Entity Type

Business

Contact Information for Business Card

Liam Porter
Construction Manager
E Liam@marshbuilding.com.au
M 0400 213 594
Mail 14 Tarrant Rise Dawesville WA 6211

```html
<!DOCTYPE html>
<html lang="en">
<head>
<meta charset="UTF-8">
<title>Marsh Building &amp; Construction – Business Card</title>
<link href="https://fonts.googleapis.com/css2?family=Inter:wght@400;700&display=swap" rel="stylesheet">
<style>
  :root {
    --bg: #e7e8ea;
    --card-white: #fcfdfd;
    --card-black: #050505;
    --ink: #1d1f33;
    --text-light: #f2f2f2;
    --accent-blue: #22bde0;
    --accent-orange: #f0861e;
  }
  * { margin: 0; padding: 0; box-sizing: border-box; }
  html, body {
    width: 1200px; height: 960px; overflow: hidden;
    background: var(--bg);
    font-family: "Inter", Arial, sans-serif;
  }
  .stage {
    width: 1200px; height: 960px;
    display: flex; align-items: center; justify-content: center; gap: 90px;
  }
  .card {
    width: 330px; height: 570px;
    border-radius: 22px;
    overflow: hidden;
    position: relative;
    background: var(--card-white);
    box-shadow: 0 10px 30px rgba(0,0,0,0.18);
  }
  /* Contact side */
  .card-contact .brand-strip {
    height: 168px;
    display: flex; align-items: center; justify-content: center;
  }
  .card-contact .info-panel {
    position: absolute; left: 0; right: 0; top: 168px; bottom: 0;
    background: var(--card-black);
    color: var(--text-light);
    padding: 44px 34px 40px;
    display: flex; flex-direction: column; justify-content: space-between;
  }
  .person-name { font-size: 24px; font-weight: 400; letter-spacing: 0.2px; }
  .person-role { font-size: 14px; font-weight: 400; margin-top: 6px; }
  .contact-list { list-style: none; font-size: 13px; line-height: 1.55; }
  /* Brand side */
  .card-brand {
    display: flex; align-items: flex-end; justify-content: center;
    padding-bottom: 130px;
  }
  /* Wordmark */
  .wordmark {
    display: flex; align-items: center; gap: 12px;
    color: var(--ink); font-weight: 700;
    text-transform: uppercase; line-height: 1.1;
  }
  .wordmark-square {
    background: var(--accent-blue); flex: none;
  }
  .wordmark-small { font-size: 15px; }
  .wordmark-small .wordmark-square { width: 14px; height: 14px; }
  .wordmark-large { font-size: 25px; }
  .wordmark-large .wordmark-square { width: 24px; height: 24px; }
</style>
</head>
<body>
<main class="stage">
  <article class="card card-contact">
    <div class="brand-strip">
      <div class="wordmark wordmark-small">
        <span class="wordmark-square"></span>
        <span>Marsh Building<br>&amp; Construction</span>
      </div>
    </div>
    <section class="info-panel">
      <header>
        <h1 class="person-name">Liam Porter</h1>
        <p class="person-role">Construction Manager</p>
      </header>
      <ul class="contact-list">
        <li>0400 213 594</li>
        <li>Liam@marshbuilding.com.au</li>
        <li>14 Tarrant Rise Dawesville WA 6211</li>
      </ul>
    </section>
  </article>

  <article class="card card-brand">
    <div class="wordmark wordmark-large">
      <span class="wordmark-square"></span>
      <span>Marsh Building<br>&amp; Construction</span>
    </div>
  </article>
</main>
</body>
</html>
```